business card deign

Logo needs the following on it.
1. attached logo
2. Tagline - "If it chills the cooler or lifts the crowd...we make it!"
3. Name- Dalton Pikes, Founder and CPO
4. Address - 412 E. Carver Avenue, Ste 2207, Tampa, FL. 33917
5. Phone - 555.318.4726

```html
<!DOCTYPE html>
<html lang="en">
<head>
<meta charset="utf-8">
<title>Kelvo Business Card</title>
<link rel="stylesheet" href="https://fonts.googleapis.com/css2?family=Montserrat:wght@400;600&display=swap">
<style>
  :root {
    --backdrop: #161616;
    --card: #2b2b2b;
    --ink: #f4f4f4;
    --ink-soft: #e6e6e6;
  }
  * { margin: 0; padding: 0; box-sizing: border-box; }
  html, body { width: 1200px; height: 1059px; overflow: hidden; }
  body {
    background: var(--backdrop);
    font-family: "Montserrat", sans-serif;
    color: var(--ink);
    position: relative;
  }
  .card {
    position: absolute;
    background: var(--card);
    border-radius: 18px;
    box-shadow: 0 8px 18px rgba(0,0,0,0.55);
  }
  .card--front { left: 257px; top: 89px; width: 687px; height: 390px; }
  .card--back  { left: 254px; top: 547px; width: 693px; height: 393px; }

  .brand {
    position: absolute;
    display: flex;
    flex-direction: column;
    align-items: center;
  }
  .brand__mark {
    border-radius: 50%;
    background: var(--ink);
  }
  .brand__name {
    font-weight: 600;
    color: var(--ink);
    text-transform: uppercase;
    line-height: 1.2;
  }
  .card--front .brand { left: 100px; top: 112px; width: 210px; }
  .card--front .brand__mark { width: 80px; height: 80px; margin-bottom: 50px; }
  .card--front .brand__name { font-size: 32px; letter-spacing: 14px; margin-right: -14px; }

  .card--back .brand { left: 0; top: 95px; width: 100%; }
  .card--back .brand__mark { width: 110px; height: 110px; margin-bottom: 40px; }
  .card--back .brand__name { font-size: 46px; letter-spacing: 20px; margin-right: -20px; }

  .divider {
    position: absolute;
    left: 338px; top: 116px;
    width: 1px; height: 162px;
    background: var(--ink-soft);
  }

  .contact { position: absolute; left: 371px; top: 112px; }
  .contact__name { font-size: 25px; font-weight: 600; letter-spacing: 0.5px; line-height: 1.1; }
  .contact__role { font-size: 16.5px; color: var(--ink-soft); margin-top: 2px; line-height: 20px; }
  .contact__address { font-size: 16.5px; color: var(--ink-soft); line-height: 23px; margin-top: 14px; }
  .contact__line {
    display: flex; align-items: center; gap: 7px;
    font-size: 16.5px; color: var(--ink-soft); line-height: 20px;
  }
  .contact__line--phone { margin-top: 12px; }
  .contact__line--email { margin-top: 6px; }
  .contact__icon { width: 12px; height: 12px; fill: var(--ink-soft); }

  .tagline {
    position: absolute;
    left: 0; top: 340px; width: 100%;
    text-align: center;
    font-size: 16.5px;
    color: var(--ink-soft);
    letter-spacing: 0.2px;
  }
</style>
</head>
<body>
  <section class="card card--front">
    <div class="brand">
      <span class="brand__mark"></span>
      <span class="brand__name">Kelvo</span>
    </div>
    <span class="divider"></span>
    <div class="contact">
      <p class="contact__name">DALTON PIKES</p>
      <p class="contact__role">Founder and CPO</p>
      <p class="contact__address">412 E. Carver Avenue<br>Ste 2207, Tampa, FL. 33917</p>
      <p class="contact__line contact__line--phone">
        <svg class="contact__icon" viewBox="0 0 12 12"><path d="M1 4c0-2 2-3 5-3s5 1 5 3v1H8.5V3.5h-5V5H1zM3 6h6l1.5 5h-9z"/></svg>
        555.318.4726
      </p>
      <p class="contact__line contact__line--email">
        <svg class="contact__icon" viewBox="0 0 12 12"><path d="M1 5l5-4 5 4v6H1z"/><path d="M1.8 5.4L6 8.4l4.2-3" fill="none" stroke="#2b2b2b" stroke-width="1"/></svg>
        daltonpikes@kelvoco.com
      </p>
    </div>
  </section>

  <section class="card card--back">
    <div class="brand">
      <span class="brand__mark"></span>
      <span class="brand__name">Kelvo</span>
    </div>
    <p class="tagline">If it chills the cooler or lifts the crowd...we make it!</p>
  </section>
</body>
</html>
```